Business card design for new eCommerce site focusing on integrity and strong businsess tactics

We need a business card that will stand out and be memorable. Something with color that matches our company logo colors. Think high end version of Pactivo. There are 2 logos provided. The parent company is called Amber Ledge Partners and we are presenting a new and very exciting eCommerce site called BrightHarborTrade.example.

Target Market(s)

Our target markets are in the Activities, Food and Beverage, Health and Beauty

Industry/Entity Type

Marketing

Contact Information for Business Card

We have 4 members that need cards...I will provide all info to the winner of the design contest
Business Address is
4870 West 63rd Avenue, Suite C207
Phoenix AZ 85731

Font styles to use
Serif
Sans Serif

Colors

Designer to choose colors to be used in the design.

Requirements
Must have
• The card must be memorable...should be unique in design but must exude integrity and be playful .
• I have provided several colors or our parent company...please feel free to use which ever
Nice to have
• I will leave this up to you. Feel free to use other images of your choosing that wraps around our client.....Activities, Dining, Health, Beauty
Should not have
• just dont be boring

```html
<!DOCTYPE html>
<html lang="en">
<head>
<meta charset="utf-8">
<title>BrightHarborTrade.example business card</title>
<link href="https://fonts.googleapis.com/css2?family=Questrial&family=PT+Sans+Narrow:wght@700&display=swap" rel="stylesheet">
<style>
  :root {
    --backdrop: #2a2a2b;
    --paper: #f3f3f3;
    --brand-blue: #2b78a8;
    --name-blue: #2d7cb2;
    --brand-green: #6cb52e;
    --ink: #555659;
    --white: #ffffff;
  }
  * { box-sizing: border-box; margin: 0; padding: 0; }
  html, body {
    width: 1200px; height: 960px; overflow: hidden;
    background: var(--backdrop);
    font-family: "Questrial", "Century Gothic", sans-serif;
  }
  .canvas { position: relative; width: 1200px; height: 960px; }

  .card {
    position: absolute; width: 600px; height: 342px; overflow: hidden;
    box-shadow: 0 3px 8px rgba(0,0,0,.45);
  }
  .card-front { left: 314px; top: 113px; background: var(--paper); }
  .card-back  { left: 311px; top: 472px; background: var(--brand-blue); }

  /* front */
  .brand { position: absolute; left: 42px; top: 138px; }
  .brand-name {
    display: flex; align-items: center; gap: 7px;
    color: var(--brand-green); font-size: 19px; line-height: 1;
  }
  .brand-dot { width: 12px; height: 12px; border-radius: 50%; background: var(--brand-blue); }
  .brand-tagline { margin: 6px 0 0 19px; font-size: 11px; color: var(--ink); letter-spacing: .4px; }

  .divider {
    position: absolute; left: 319px; top: 78px; width: 2px; height: 166px;
    background: linear-gradient(to bottom, transparent, #b9b9b9 20%, #b9b9b9 80%, transparent);
  }
  .contact { position: absolute; left: 345px; top: 80px; color: var(--ink); }
  .person-name {
    font-family: "PT Sans Narrow", "Arial Narrow", sans-serif; font-weight: 700;
    font-size: 24px; color: var(--name-blue); letter-spacing: .3px; line-height: 1;
  }
  .person-title { font-size: 15px; color: var(--brand-green); margin-top: 3px; letter-spacing: .2px; }
  .address { margin-top: 11px; font-size: 14px; line-height: 18px; }
  .lines { list-style: none; margin-top: 9px; font-size: 14px; line-height: 19.5px; }
  .lines li { display: flex; align-items: center; gap: 8px; }
  .lines svg { width: 13px; height: 13px; fill: var(--brand-blue); }

  .band { position: absolute; left: 0; bottom: 0; width: 600px; height: 80px; }
  .web {
    position: absolute; left: 0; right: 0; bottom: 8px; text-align: center;
    color: var(--white); font-size: 13px; letter-spacing: 4.2px;
  }

  /* back */
  .parent-mark {
    position: absolute; left: 264px; top: 70px; width: 72px; height: 72px;
    border: 4px solid var(--white); border-radius: 50%;
  }
  .parent-name {
    position: absolute; left: 0; right: 0; top: 218px; text-align: center;
    color: var(--white); font-size: 34px; letter-spacing: .5px;
  }
</style>
</head>
<body>
<main class="canvas">
  <section class="card card-front" aria-label="Card front">
    <div class="brand">
      <div class="brand-name"><span class="brand-dot"></span>BrightHarborTrade.example</div>
      <div class="brand-tagline">Local Deals for Everyday Living</div>
    </div>

    <div class="divider"></div>

    <div class="contact">
      <div class="person-name">DANIEL REYES</div>
      <div class="person-title">CEO/FOUNDER</div>
      <p class="address">4870 West 63rd Avenue<br>Suite C207, Phoenix AZ 85731</p>
      <ul class="lines">
        <li><svg viewBox="0 0 24 24" aria-hidden="true"><path d="M6.6 10.8a15 15 0 0 0 6.6 6.6l2.2-2.2a1 1 0 0 1 1-.25 11.4 11.4 0 0 0 3.6.57 1 1 0 0 1 1 1V20a1 1 0 0 1-1 1A17 17 0 0 1 3 4a1 1 0 0 1 1-1h3.5a1 1 0 0 1 1 1c0 1.25.2 2.45.57 3.57a1 1 0 0 1-.25 1z"/></svg>602 555 0148</li>
        <li><svg viewBox="0 0 24 24" aria-hidden="true"><path d="M7 1h10a2 2 0 0 1 2 2v18a2 2 0 0 1-2 2H7a2 2 0 0 1-2-2V3a2 2 0 0 1 2-2zm0 3v14h10V4zm5 15.5a1.2 1.2 0 1 0 0 2.4 1.2 1.2 0 0 0 0-2.4z"/></svg>602 555 0193</li>
        <li><svg viewBox="0 0 24 24" aria-hidden="true"><path d="M2 5h20v14H2zm2 2v.5l8 5 8-5V7zm0 2.8V17h16V9.8l-8 5z"/></svg>daniel@brightharbortrade.example</li>
      </ul>
    </div>

    <svg class="band" viewBox="0 0 600 80" preserveAspectRatio="none" aria-hidden="true">
      <path d="M0 22 Q300 70 600 22 L600 80 L0 80 Z" fill="var(--brand-blue)"/>
      <path d="M40 28 Q300 58 560 28" fill="none" stroke="var(--brand-green)" stroke-width="3"/>
    </svg>
    <div class="web">www.brightharbortrade.example</div>
  </section>

  <section class="card card-back" aria-label="Card back">
    <span class="parent-mark"></span>
    <div class="parent-name">Amber Ledge Partners</div>
  </section>
</main>
</body>
</html>
```